Local fast-growing company in the service sector

We are looking for a modern business card design, which should also appear on our letterheads

Target Market(s)

Private and industrial sectors

Contact Information for Business Card

Vorname Name
Kellberger Str. 18
74389 Lindenfeld
Tel.: 07146-839214-0
Name@agentur-kvtl.de

Colors
9d9d9d
919191
aaaaaa

Requirements
Must have
• The logo (file) in silver

```html
<!DOCTYPE html>
<html lang="de">
<head>
<meta charset="utf-8">
<title>KVTL – Visitenkarte</title>
<link href="https://fonts.googleapis.com/css2?family=Open+Sans:wght@400&display=swap" rel="stylesheet">
<style>
  :root {
    --page: #ffffff;
    --card-light: #f1f2f2;
    --card-mid: #d9dbdb;
    --panel: #ffffff;
    --silver: #aaaaaa;
    --brand-text: #919191;
    --contact-text: #5f6b6e;
  }
  html, body {
    margin: 0;
    width: 1200px;
    height: 685px;
    overflow: hidden;
    background: var(--page);
    font-family: "Open Sans", sans-serif;
  }
  .canvas {
    position: relative;
    width: 1200px;
    height: 685px;
  }
  .card {
    position: absolute;
    left: 39px;
    top: 32px;
    width: 1161px;
    height: 623px;
    border-radius: 44px 0 44px 0;
    overflow: hidden;
    box-shadow: 0 2px 6px rgba(0,0,0,0.12);
  }
  .card-background {
    position: absolute;
    inset: 0;
    background:
      radial-gradient(ellipse 30% 40% at 12% 30%, rgba(150,150,150,0.55), transparent 70%),
      radial-gradient(ellipse 22% 50% at 88% 30%, rgba(150,150,150,0.4), transparent 70%),
      linear-gradient(180deg, var(--card-light) 0%, var(--card-mid) 55%, var(--card-light) 100%);
  }
  .logo-panel {
    position: absolute;
    left: 161px;
    top: 21px;
    width: 823px;
    height: 296px;
    background: var(--panel);
    box-shadow: 0 14px 30px rgba(0,0,0,0.35);
  }
  .brand-mark {
    position: absolute;
    left: 40px;
    top: 58px;
    width: 190px;
    height: 190px;
    background: var(--silver);
  }
  .brand-name,
  .brand-web {
    position: absolute;
    left: 294px;
    color: var(--brand-text);
    font-weight: 400;
    line-height: 1;
    white-space: nowrap;
  }
  .brand-name {
    top: 77px;
    font-size: 156px;
    letter-spacing: 22px;
  }
  .brand-web {
    top: 222px;
    font-size: 42px;
    letter-spacing: 10px;
  }
  .contact {
    position: absolute;
    left: 0;
    right: 0;
    top: 354px;
    margin: 0;
    text-align: center;
    font-style: normal;
    font-size: 32px;
    line-height: 47px;
    color: var(--contact-text);
  }
</style>
</head>
<body>
  <div class="canvas">
    <div class="card">
      <div class="card-background" role="img" aria-label="Heller silbergrauer Hintergrund mit dezentem Dreiecksmuster"></div>
      <div class="logo-panel">
        <div class="brand-mark"></div>
        <span class="brand-name">KVTL</span>
        <span class="brand-web">agentur-kvtl.de</span>
      </div>
      <address class="contact">
        Vorname Name<br>
        Kellberger Str. 18<br>
        74389 Lindenfeld<br>
        Tel.: 07146-839214-0<br>
        Name@agentur-kvtl.de
      </address>
    </div>
  </div>
</body>
</html>
```